BOLD & MINIMALIST DESIGN NEEDED

We want a very bold but minimalistic business card design that is impactful and utilizes both sides of the business card. Our current logo is included for your use.

We want bold fonts and good use of negative space. We don't want the logo to overpower the design.

Target Market(s)

Professionals who are building new commercial buildings.

Industry/Entity Type

Construction

Contact Information for Business Card

Name, Title, email, office phone, cell phone, website

Font styles to use
Serif
Sans Serif

Requirements
Must have
• Bold design!

```html
<!DOCTYPE html>
<html lang="en">
<head>
<meta charset="utf-8">
<title>Ridgeline Design + Build — Business Card</title>
<link rel="stylesheet" href="https://fonts.googleapis.com/css2?family=Montserrat:wght@400;500;700;800&display=swap">
<style>
  :root {
    --green: #84c441;
    --ink: #111111;
    --paper: #ffffff;
    --stage: #3a3a3a;
    --rule: #1b1f3a;
  }
  * { box-sizing: border-box; margin: 0; padding: 0; }
  html, body {
    width: 1200px; height: 689px; overflow: hidden;
    background: var(--stage);
    font-family: "Montserrat", Arial, sans-serif;
  }
  .canvas { position: relative; width: 1200px; height: 689px; }
  .card {
    position: absolute; top: 190px;
    width: 540px; height: 309px;
    border-radius: 22px; overflow: hidden;
  }
  .card--front { left: 40px; background: var(--green); }
  .card--back { left: 620px; background: var(--paper); }

  /* Front */
  .front-brand {
    position: absolute; inset: 0;
    display: flex; flex-direction: column; align-items: center; justify-content: center;
    color: var(--paper); font-weight: 800; text-transform: uppercase; line-height: 1;
  }
  .front-brand__name { font-size: 66px; letter-spacing: 1px; }
  .front-brand__tag { font-size: 24px; letter-spacing: 9px; margin-top: 14px; }

  /* Back */
  .back-band { position: absolute; inset: 0; width: 100%; height: 100%; }
  .back-brand {
    position: absolute; top: 26px; left: 150px; width: 300px;
    text-align: center; color: var(--ink); font-weight: 800; text-transform: uppercase; line-height: 1;
  }
  .back-brand__name { font-size: 34px; letter-spacing: 0.5px; }
  .back-brand__tag { font-size: 12px; letter-spacing: 5px; margin-top: 6px; }

  .person {
    position: absolute; left: 20px; top: 128px; width: 256px; text-align: right;
    white-space: nowrap; line-height: 1.1;
  }
  .person__name { font-size: 26px; font-weight: 800; color: var(--green); letter-spacing: 0.5px; }
  .person__title { font-size: 13px; font-weight: 500; color: var(--ink); letter-spacing: 1px; margin-top: 4px; }

  .divider {
    position: absolute; left: 290px; top: 100px; width: 1.5px; height: 84px; background: var(--rule);
  }
  .contacts {
    position: absolute; left: 304px; top: 100px; list-style: none;
    font-size: 12.5px; color: var(--ink); font-weight: 400; white-space: nowrap;
  }
  .contacts li { display: flex; align-items: center; gap: 7px; height: 21px; }
  .contacts svg { width: 11px; height: 11px; flex: none; fill: var(--green); }

  .address {
    position: absolute; right: 30px; bottom: 18px;
    color: var(--paper); font-size: 13px; font-weight: 500; white-space: nowrap;
  }
</style>
</head>
<body>
<main class="canvas">

  <section class="card card--front" aria-label="Card front">
    <div class="front-brand">
      <span class="front-brand__name">Ridgeline</span>
      <span class="front-brand__tag">Design + Build</span>
    </div>
  </section>

  <section class="card card--back" aria-label="Card back">
    <svg class="back-band" viewBox="0 0 540 309" preserveAspectRatio="none" aria-hidden="true">
      <path d="M0,309 L0,290 Q330,282 540,170 L540,309 Z" fill="var(--green)"/>
      <path d="M60,280 Q340,262 525,168" fill="none" stroke="var(--ink)" stroke-width="3" stroke-linecap="round"/>
    </svg>

    <div class="back-brand">
      <div class="back-brand__name">Ridgeline</div>
      <div class="back-brand__tag">Design + Build</div>
    </div>

    <div class="person">
      <div class="person__name">MARCUS HALE</div>
      <div class="person__title">OWNER-CEO</div>
    </div>

    <div class="divider"></div>

    <ul class="contacts">
      <li><svg viewBox="0 0 12 12"><path d="M1 4 Q6 0 11 4 L9 5.5 L8 4 L4 4 L3 5.5 Z M2.5 7 L9.5 7 L10 11 L2 11 Z"/></svg>123 456 789</li>
      <li><svg viewBox="0 0 12 12"><path d="M3 0 H9 V12 H3 Z M4 1.5 V9.5 H8 V1.5 Z" fill-rule="evenodd"/></svg>123 456 789</li>
      <li><svg viewBox="0 0 12 12"><path d="M0 2 H12 V10 H0 Z M1 3 L6 6.5 L11 3 Z" fill-rule="evenodd"/></svg>info@yourgmail.com</li>
      <li><svg viewBox="0 0 12 12"><circle cx="6" cy="6" r="5.5"/></svg>www.yourwebsite.com</li>
    </ul>

    <div class="address">Your address, City State, Zip 1234</div>
  </section>

</main>
</body>
</html>
```